New template needed for Joomla 3.2 website

We are a mortgage origination company based in Johannesburg, South Africa and require a sleek, modern & professional look for our website.
The website is complete and your template should accommodate all pages on the site (there are not many) and be ready for Joomla implementation.
Our website can be viewed at www.keystonebondhub.co.za
Target Market(s)
We are targeting consumers who require mortgage finance to buy real estate. There is no particular demographic, except that we cater to South African home buyers exclusively!
Requirements
Must have
- It must look professional and modern.
Take a look at competitor websites:
www.ziva.co.za
www.pkbondfinder.com
http://www.tallwavegroup.co.za/bondpeak/
http://www.ridgeloan.co.za/
We want to beat the competition !!
Nice to have
- Website should blend with company logo and play on the symbol in the logo.
I want more of a people / photo element to the template. It needs to make us seem "tangible"

```html
<!DOCTYPE html>
<html lang="en">
<head>
<meta charset="utf-8">
<title>Keystone Bond Hub</title>
<link href="https://fonts.googleapis.com/css2?family=Roboto:wght@400;500;700&display=swap" rel="stylesheet">
<style>
:root{
  --blue:#2f74bd;
  --blue-dark:#1d5aa0;
  --blue-text:#2569b2;
  --grey-text:#8a8a8a;
  --dark-text:#444;
  --band:#f3f3f3;
  --footer:#2b2b2b;
  --footer-bottom:#232323;
  --footer-text:#8d8d8d;
  --white:#fff;
}
*{margin:0;padding:0;box-sizing:border-box}
html,body{width:715px;height:1200px;overflow:hidden;background:var(--white)}
body{position:relative;font-family:'Roboto',Arial,sans-serif;color:var(--dark-text)}
.abs{position:absolute}

.header{top:0;left:0;width:715px;height:69px}
.brand{left:78px;top:24px;display:flex;align-items:center;gap:6px}
.brand-dot{width:22px;height:22px;border-radius:50%;background:var(--blue)}
.brand-name{font-size:17px;font-weight:700;color:var(--blue);letter-spacing:.2px}
.callus{right:78px;top:23px;text-align:left}
.callus small{display:block;font-size:9px;color:#555;font-weight:500}
.callus b{display:block;font-size:16px;color:var(--blue);font-weight:700}

.nav{top:69px;left:0;width:715px;height:31px;background:var(--blue)}
.nav ul{list-style:none;position:absolute;left:78px;top:0;display:flex;height:31px}
.nav li{font-size:7.5px;color:var(--white);line-height:31px;padding:0 13px;text-transform:uppercase}
.nav li.active{background:var(--blue-dark);padding:0 15px}
.nav li:nth-child(3){padding-right:29px}

.hero{top:100px;left:0;width:715px;height:255px;overflow:hidden;
  background:linear-gradient(100deg,#b9cde0 0%,#d8e2ea 35%,#c9b29a 62%,#e2c6a6 75%,#9ab2cc 100%)}
.hero-arrow{top:99px;width:46px;height:46px;border-radius:50%;background:var(--blue);border:2px solid var(--white)}
.hero-arrow.left{left:-24px}
.hero-arrow.right{right:-24px}
.hero-arrow svg{position:absolute;top:14px}
.hero-arrow.left svg{right:8px}
.hero-arrow.right svg{left:8px}
.hero h1{left:83px;top:204px;font-size:15.5px;color:var(--white);font-weight:700}
.hero p{left:83px;top:225px;font-size:9px;color:var(--white);font-weight:500}

.section-head{left:0;width:715px;text-align:center}
.section-head h2{font-size:11px;font-weight:500;color:var(--blue-text);text-transform:uppercase;letter-spacing:.2px}
.section-head p{font-size:7.5px;color:var(--grey-text);margin-top:6px}

.features{top:416px;left:0;width:715px;height:181px;background:var(--band);display:flex}
.feature{flex:none;text-align:center;border-right:1px solid #e2e2e2;position:relative}
.feature:last-child{border-right:none}
.feature svg{display:block;margin:30px auto 0;height:30px}
.feature h3{font-size:10.5px;font-weight:500;color:var(--blue-text);margin-top:9px}
.feature p{font-size:7px;line-height:11px;color:var(--grey-text);width:110px;margin:12px auto 0}
.btn{display:inline-block;background:var(--blue);color:var(--white);font-size:6.5px;font-weight:500;width:58px;height:18px;line-height:18px;margin-top:11px;text-transform:uppercase}

.perk{top:663px;width:179px;height:89px;background:var(--blue);color:var(--white)}
.perk-img{left:8px;top:8px;width:50px;height:48px;border-radius:4px}
.perk h4{left:62px;top:11px;font-size:9.5px;font-weight:500;text-transform:uppercase}
.perk p{left:62px;top:31px;width:110px;font-size:6px;line-height:9.3px}
.perk-btn{left:14px;top:62px;width:38px;height:14px;border:1px solid var(--white);font-size:6px;text-align:center;line-height:12px}

.rule{height:1px;background:#e4e4e4}
.col-title{top:801px;font-size:10.5px;font-weight:500;color:var(--blue-text);text-transform:uppercase}
.item-img{width:73px;height:67px;border:1px solid #ddd;border-radius:2px}
.item-title{font-size:9px;color:#555}
.item-text{font-size:6.6px;line-height:11px;color:var(--grey-text);width:160px}

.footer{top:1033px;left:0;width:715px;height:127px;background:var(--footer)}
.footer-brand{left:78px;top:22px;display:flex;align-items:center;gap:5px}
.footer-brand .brand-dot{width:18px;height:18px;background:#bbb}
.footer-brand .brand-name{font-size:13px;color:#ccc}
.footer-about{left:78px;top:55px;width:150px;font-size:6.8px;line-height:11px;color:var(--footer-text)}
.footer h5{top:24px;font-size:10.5px;font-weight:500;color:var(--white)}
.footer-list{top:55px;width:95px;list-style:none}
.footer-list li{font-size:6.5px;color:var(--footer-text);border-bottom:1px solid #3d3d3d;padding:0 0 6px;margin-bottom:7px}
.footer-list li:last-child{border-bottom:none}
.post{font-size:6.5px;color:var(--footer-text);line-height:10px}
.post b{display:block;color:#ddd;font-weight:400;font-size:6px}
.contact{left:526px;top:55px;font-size:6.5px;line-height:13.5px;color:var(--footer-text)}
.contact b{color:#ddd;font-weight:400}

.bottom{top:1160px;left:0;width:715px;height:40px;background:var(--footer-bottom)}
.bottom-links{left:81px;top:15px;font-size:6.5px;color:#ccc;display:flex;gap:7px}
.bottom-links span.copy{color:#aaa}
.socials{left:519px;top:15px;display:flex;gap:6px}
.socials i{display:block;width:11px;height:11px;border-radius:50%;background:#ddd}
</style>
</head>
<body>

<header class="header abs">
  <div class="brand abs"><span class="brand-dot"></span><span class="brand-name">KEYSTONE BOND HUB</span></div>
  <div class="callus abs"><small>CALL US:</small><b>(011) 482 7735</b></div>
</header>

<nav class="nav abs">
  <ul>
    <li class="active">Home</li>
    <li>About Keystone</li>
    <li>Important Information</li>
    <li>Homeloan Calculators</li>
    <li>Apply On-line</li>
    <li>Contact Keystone</li>
  </ul>
</nav>

<section class="hero abs" role="img" aria-label="Photo of a red house with a yellow roof and a hand holding a golden key with a house-shaped keyring">
  <div class="hero-arrow left abs"><svg width="10" height="14" viewBox="0 0 10 14"><path d="M8 1 2 7l6 6" stroke="#fff" stroke-width="3" fill="none"/></svg></div>
  <div class="hero-arrow right abs"><svg width="10" height="14" viewBox="0 0 10 14"><path d="M2 1l6 6-6 6" stroke="#fff" stroke-width="3" fill="none"/></svg></div>
  <h1 class="abs">WE RAISE YOUR HOME LOAN WITH:</h1>
  <p class="abs">KELDARA . VANTRO BANK . OSMERE . BRELLIN . TAVISTRA . QUORVEN . DORVALLIS</p>
</section>

<div class="section-head abs" style="top:375px">
  <h2>Neque porro quisquam est qui dolorem ipsum</h2>
  <p>Sed ut perspiciatis unde omnis iste natus error sit voluptatem accusantium doloremque</p>
</div>

<section class="features abs">
  <div class="feature" style="width:209px">
    <svg width="28" height="30" viewBox="0 -1 28 30" fill="#777"><circle cx="11" cy="8" r="6"/><path d="M0 27c0-7 5-11 11-11s10 3 11 8H0z"/><path d="M21 14h2v3h3v2h-3v3h-2v-3h-3v-2h3z"/></svg>
    <h3>Referral Program</h3>
    <p>Click on the button below to join our lead referal program and start earning money.</p>
    <span class="btn">Join Today</span>
  </div>
  <div class="feature" style="width:151px">
    <svg width="30" height="30" viewBox="0 -1 30 30" fill="#777"><path d="M3 22 18 5l5 4L9 25l-7 2z"/><rect x="18" y="15" width="11" height="10"/></svg>
    <h3>Get Pre Qualified</h3>
    <p>Click on the button below to join our lead referal program and start earning money.</p>
    <span class="btn">Apply Now</span>
  </div>
  <div class="feature" style="width:152px">
    <svg width="24" height="30" viewBox="0 0 24 30"><path d="M5 9a7 7 0 1 1 10 6c-2 1-3 2-3 5" stroke="#777" stroke-width="4" fill="none"/><circle cx="12" cy="27" r="2.5" fill="#777"/></svg>
    <h3>Ask a Question</h3>
    <p>Click on the button below to join our lead referal program and start earning money.</p>
    <span class="btn">Ask Now</span>
  </div>
  <div class="feature" style="width:203px">
    <svg width="26" height="30" viewBox="0 -1 26 30" fill="none" stroke="#777" stroke-width="2"><rect x="1" y="1" width="24" height="26"/><rect x="5" y="5" width="16" height="6"/><path d="M5 15h4M11 15h4M17 15h4M5 19h4M11 19h4M17 19h4M5 23h4M11 23h4M17 23h4"/></svg>
    <h3>Calculators</h3>
    <p>Click on the button below to join our lead referal program and start earning money.</p>
    <span class="btn">Calculate</span>
  </div>
</section>

<div class="section-head abs" style="top:622px">
  <h2>Fast Homeloans . Great Service !</h2>
  <p>Sed ut perspiciatis unde omnis iste natus error sit voluptatem accusantium doloremque</p>
</div>

<article class="perk abs" style="left:78px">
  <div class="perk-img abs" role="img" aria-label="Illustration of a bank building" style="background:linear-gradient(#e6e6e6,#9a9a9a)"></div>
  <h4 class="abs">100% Free of Charge</h4>
  <p class="abs">No hidden costs or service charges. Our fee is not hidden within the finance charges of your homeloan. We guarantee a 100% free of .... charge, first class service to you.</p>
  <span class="perk-btn abs">MORE</span>
</article>
<article class="perk abs" style="left:268px">
  <div class="perk-img abs" style="left:14px;top:11px;width:40px;height:40px;border-radius:50%;background:#e8b81f"></div>
  <h4 class="abs">Exceptional Service</h4>
  <p class="abs">We guarantee a first class service to you. Our home loan specialists are up to date with the latest finance criteria from all the major financial</p>
  <span class="perk-btn abs">MORE</span>
</article>
<article class="perk abs" style="left:458px">
  <div class="perk-img abs" role="img" aria-label="Illustration of a broken blue debit card" style="width:42px;background:linear-gradient(#6fb2e8,#1f5fa4)"></div>
  <h4 class="abs">Credit Help</h4>
  <p class="abs">Problems with your credit record? We will do our best to help you into the clear with sound advice. We will refer you to attorneys and other business</p>
  <span class="perk-btn abs">MORE</span>
</article>

<div class="rule abs" style="top:780px;left:0;width:715px"></div>

<h3 class="col-title abs" style="left:78px">Keystone Lead Referral Program</h3>
<h3 class="col-title abs" style="left:388px">Keystone Card</h3>

<div class="item-img abs" style="left:78px;top:828px;background:linear-gradient(120deg,#fff 10%,#d23a36 40%,#3a78c4 70%,#fff 95%)" role="img" aria-label="Horseshoe magnet attracting small blue figures"></div>
<div class="item-title abs" style="left:168px;top:834px">Origination &amp; Homeloans Explained</div>
<p class="item-text abs" style="left:168px;top:853px">We invite members of the public, estate agents, attorneys, property developers and all other property professionals to refer leads to us.</p>

<div class="rule abs" style="top:916px;left:78px;width:248px"></div>

<div class="item-img abs" style="left:78px;top:940px;background:linear-gradient(160deg,#fff 15%,#c49a66 50%,#4d8fd6 75%,#fff 95%)" role="img" aria-label="Cardboard box full of small blue figures"></div>
<div class="item-title abs" style="left:168px;top:946px">Origination &amp; Homeloans Explained</div>
<p class="item-text abs" style="left:168px;top:965px">We invite members of the public, estate agents, attorneys, property developers and all other property professionals to refer leads to us.</p>

<div class="abs" style="left:357px;top:840px;width:1px;height:152px;background:#e0e0e0"></div>

<div class="item-img abs" style="left:387px;top:828px;background:linear-gradient(90deg,#fff 15%,#e2803c 40%,#3a3a3a 55%,#5aa0d8 75%,#fff 95%)" role="img" aria-label="Woman carrying colourful shopping bags"></div>
<div class="item-title abs" style="left:478px;top:834px">Origination &amp; Homeloans Explained</div>
<p class="item-text abs" style="left:478px;top:853px">We invite members of the public, estate agents, attorneys, property developers and all other property professionals to refer leads to us.</p>

<div class="rule abs" style="top:916px;left:387px;width:248px"></div>

<div class="item-img abs" style="left:387px;top:940px;background:linear-gradient(150deg,#fff 10%,#49a8e0 40%,#1c5a9c 75%,#fff 95%)" role="img" aria-label="Two blue payment cards"></div>
<div class="item-title abs" style="left:478px;top:946px">Origination &amp; Homeloans Explained</div>
<p class="item-text abs" style="left:478px;top:965px">We invite members of the public, estate agents, attorneys, property developers and all other property professionals to refer leads to us.</p>

<footer class="footer abs">
  <div class="footer-brand abs"><span class="brand-dot"></span><span class="brand-name">KEYSTONE BOND HUB</span></div>
  <p class="footer-about abs">Lorem ipsum dolor sit amet, consectetuer adipiscing elit, sed diam nonummy nibh euis-mod tincidunt ut laoreet dolore magna aliquam erat volutpatLorem ipsum dolor sit amet</p>

  <h5 class="abs" style="left:249px">Recent Comments</h5>
  <ul class="footer-list abs" style="left:249px">
    <li>harlow on Blue Falcon server</li>
    <li>harlow on Black Falcon Skull</li>
    <li>harlow on Black Falcon Skull</li>
  </ul>

  <h5 class="abs" style="left:388px">Recent posts</h5>
  <ul class="footer-list abs" style="left:388px">
    <li class="post">Advanced cloud security servers<b>February 11, 2014</b></li>
    <li class="post">Advanced cloud security servers<b>February 11, 2014</b></li>
  </ul>

  <h5 class="abs" style="left:526px">Contact info</h5>
  <div class="contact abs">
    Suite 7 Fernhill Court, Willow Lane,<br>
    Brackenview, 2094<br>
    <b>Tel:</b> (011) 482 7735<br>
    <b>Hours:</b> 8 AM - 5 PM Monday - Friday
  </div>
</footer>

<div class="bottom abs">
  <div class="bottom-links abs">
    <span>Privacy Policy</span><span>About Keystone</span><span>Contact Keystone</span>
    <span class="copy">Copyright © 2014 Keystone Bond Hub (Pty) Ltd</span>
  </div>
  <div class="socials abs"><i></i><i></i><i></i><i></i><i></i><i></i><i></i></div>
</div>

</body>
</html>
```